Harborline Auto LLC

Car Dealer Customer Service
Address: 2874 Cresthaven Road, Shelbyville, TN 37162
web: www.harborlineautoxq.net
email: harborlineautoxq@mailnest.example
Phone: (931) 555-0148
Phone: (629) 555-0173

```html
<!DOCTYPE html>
<html lang="en">
<head>
<meta charset="utf-8">
<title>Harborline Auto — Business Card</title>
<link rel="stylesheet" href="https://fonts.googleapis.com/css2?family=Lexend:wght@600;700&family=Poppins:ital,wght@0,400;1,400&display=swap">
<style>
  :root {
    --backdrop: #2a2a2a;
    --card: #f1f1f1;
    --brand-blue: #1f86c4;
    --navy: #18557f;
    --gold: #e2a93a;
    --ink: #1c1c1c;
  }
  * { box-sizing: border-box; margin: 0; padding: 0; }
  html, body { width: 1200px; height: 576px; overflow: hidden; }
  body {
    background: var(--backdrop);
    position: relative;
    font-family: "Poppins", sans-serif;
    color: var(--ink);
  }
  .card {
    position: absolute;
    top: 139px;
    width: 484px;
    height: 292px;
    background: var(--card);
    border-radius: 10px;
    overflow: hidden;
  }
  .card--front { left: 102px; }
  .card--back { left: 596px; }

  .brand-name {
    position: absolute;
    font-family: "Lexend", sans-serif;
    font-weight: 700;
    font-size: 28px;
    letter-spacing: 0.5px;
    color: var(--brand-blue);
    text-transform: uppercase;
    line-height: 1;
  }
  .card--front .brand-name { left: 26px; top: 26px; }
  .card--back .brand-name { right: 26px; bottom: 40px; }

  .tagline {
    position: absolute;
    left: 26px; top: 103px;
    font-style: italic;
    font-size: 13px;
  }
  .phones {
    position: absolute;
    left: 26px; top: 125px;
    list-style: none;
  }
  .phones li {
    display: flex; align-items: center; gap: 9px;
    font-family: "Lexend", sans-serif;
    font-weight: 600;
    font-size: 17px;
    color: var(--navy);
    height: 23px;
  }
  .contacts {
    position: absolute;
    left: 26px; top: 206px;
    list-style: none;
    font-size: 12.5px;
  }
  .contacts li { display: flex; align-items: center; gap: 9px; height: 17.5px; }
  .contacts li.address { margin-top: 3px; }
  .icon { flex: none; fill: var(--gold); }

  .mark {
    position: absolute;
    left: 330px; top: 128px;
    display: flex; align-items: center; gap: 8px;
  }
  .mark-dot {
    width: 18px; height: 18px; border-radius: 50%;
    background: var(--brand-blue);
  }
  .mark-name {
    font-family: "Lexend", sans-serif;
    font-weight: 700;
    font-size: 15px;
    color: var(--gold);
  }
</style>
</head>
<body>
  <section class="card card--front" aria-label="Business card front">
    <h1 class="brand-name">Harborline Auto</h1>
    <p class="tagline">Car Dealer Customer Service</p>
    <ul class="phones">
      <li>
        <svg class="icon" width="14" height="12" viewBox="0 0 14 12" aria-hidden="true"><path d="M1 4c0-2 2-3 6-3s6 1 6 3v1h-3V3.5H4V5H1z"/><path d="M3 6h8l1.5 5h-11z"/></svg>
        931-555-0148
      </li>
      <li>
        <svg class="icon" width="14" height="12" viewBox="0 0 14 12" aria-hidden="true"><path d="M1 4c0-2 2-3 6-3s6 1 6 3v1h-3V3.5H4V5H1z"/><path d="M3 6h8l1.5 5h-11z"/></svg>
        629-555-0173
      </li>
    </ul>
    <ul class="contacts">
      <li>
        <svg class="icon" width="11" height="8" viewBox="0 0 11 8" aria-hidden="true"><path d="M0 0h11v8H0z"/><path d="M0 0l5.5 4.5L11 0" fill="none" stroke="#f1f1f1" stroke-width="1"/></svg>
        www.harborlineautoxq.net
      </li>
      <li>
        <svg class="icon" width="11" height="11" viewBox="0 0 11 11" aria-hidden="true"><circle cx="5.5" cy="5.5" r="5"/><path d="M0.5 5.5h10M5.5 0.5c-2.5 3-2.5 7 0 10M5.5 0.5c2.5 3 2.5 7 0 10" fill="none" stroke="#f1f1f1" stroke-width="0.8"/></svg>
        harborlineautoxq@mailnest.example
      </li>
      <li class="address">2874 Cresthaven Road, Shelbyville, TN 37162</li>
    </ul>
    <div class="mark">
      <span class="mark-dot"></span>
      <span class="mark-name">Harborline Auto</span>
    </div>
  </section>

  <section class="card card--back" aria-label="Business card back">
    <p class="brand-name">Harborline Auto</p>
  </section>
</body>
</html>
```